Open sky harmony Business cards - yoga studio

We need business cards for our yoga studio Opensky Harmony.
We would like to see designs that include the colour blue and our logo.
The business card should communicate a feeling of strength and calm

Requirements
Must have
• The business card must include
"Mirela Thornquist - Director"
and
"42 Wattlecrest Avenue
Dunmoreton
VIC 3917
Ph - 0471 586 204"

```html
<!DOCTYPE html>
<html lang="en">
<head>
<meta charset="utf-8">
<title>Opensky Harmony – Business Cards</title>
<link rel="stylesheet" href="https://fonts.googleapis.com/css2?family=Open+Sans:wght@300;400;700&display=swap">
<style>
  :root {
    --teal: #5aabbb;
    --card-white: #f7f7f7;
    --ink: #1f1f1f;
    --backdrop: #e9e6e3;
  }
  * { margin: 0; padding: 0; box-sizing: border-box; }
  html, body {
    width: 1200px;
    height: 997px;
    overflow: hidden;
    background: var(--backdrop);
    font-family: "Open Sans", sans-serif;
  }
  .sheet {
    position: relative;
    width: 1200px;
    height: 997px;
  }
  .card {
    position: absolute;
    top: 355px;
    width: 500px;
    height: 286px;
    box-shadow: 0 2px 6px rgba(0,0,0,0.12);
  }
  .card--front {
    left: 70px;
    background: var(--teal);
    display: flex;
    align-items: center;
    justify-content: center;
    gap: 18px;
  }
  .brand-dot {
    width: 46px;
    height: 46px;
    border-radius: 50%;
    background: #ffffff;
  }
  .brand-name {
    color: #ffffff;
    font-weight: 300;
    font-size: 40px;
    letter-spacing: 1px;
  }
  .card--back {
    left: 630px;
    background: var(--card-white);
    overflow: hidden;
  }
  .back-disc {
    position: absolute;
    left: 30px;
    top: 70px;
    width: 190px;
    height: 190px;
    border-radius: 50%;
    background: var(--teal);
  }
  .contact {
    position: absolute;
    left: 275px;
    top: 34px;
    color: var(--ink);
    font-size: 14px;
    line-height: 1.35;
  }
  .contact__name {
    font-weight: 700;
    font-size: 17px;
  }
  .contact__role {
    color: var(--teal);
    font-size: 15px;
    margin-bottom: 6px;
  }
</style>
</head>
<body>
  <main class="sheet">
    <section class="card card--front" aria-label="Card front">
      <span class="brand-dot" aria-hidden="true"></span>
      <span class="brand-name">Opensky Harmony</span>
    </section>

    <section class="card card--back" aria-label="Card back">
      <span class="back-disc" aria-hidden="true"></span>
      <div class="contact">
        <p class="contact__name">Mirela Thornquist</p>
        <p class="contact__role">Director</p>
        <p>42 Wattlecrest Avenue</p>
        <p>Dunmoreton, VIC 3917</p>
        <p>ph 0471 586 204</p>
      </div>
    </section>
  </main>
</body>
</html>
```